Business Cards for company that supports physicians that do medical research

Need to create a business card for Qorvel Studies (www.qorvelstudies.example), a company devoted to supporting physicians who conduct medical research. The form of the card should match the message of research and information quest. I have provided the logo of the company as an uploaded file. Designs should be simple and slick aimed at very high end clients.

Target Market(s)

Medical doctors that are also researchers

Industry/Entity Type

Medical

Contact Information for Business Card

Should feature logo and fields for personal info:
Name/title
Phone /email

Font styles to use
Serif
Sans Serif

Requirements
Must have
• Qorvel logo and fields for personal info:
• Name: Bertrand Okonfu
• Title: VP Research and Senior Analyst
• Phone: 555-203-4719
• email: info@qorvelstudies.example
Nice to have
• Interesting cards that I've seen:
• 1- all black/charcoal or very dark background
• 2- Plastic - semi-transparent
• 3- non-standard height-width ratios
• 4- Functional cards -- USB drive incorporated
Should not have
• Too busy; needs to stay very simple

```html
<!DOCTYPE html>
<html lang="en">
<head>
<meta charset="utf-8">
<title>Qorvel Studies – Business Card</title>
<link rel="stylesheet" href="https://fonts.googleapis.com/css2?family=Lato:wght@400;700&display=swap">
<style>
  :root {
    --page-bg: #e9e9eb;
    --card-dark: #262626;
    --card-dark-edge: #1c1c1c;
    --card-white: #ffffff;
    --silver-light: #f2f2f2;
    --silver-mid: #bdbdbd;
    --silver-deep: #8a8a8a;
    --brand-green: #3cb93a;
    --brand-blue: #1a7fd1;
    --text-light: #ffffff;
    --text-soft: #d6d6d6;
  }
  * { box-sizing: border-box; margin: 0; padding: 0; }
  html, body {
    width: 1200px;
    height: 900px;
    overflow: hidden;
    background: var(--page-bg);
    font-family: "Lato", "Helvetica Neue", Arial, sans-serif;
  }
  .canvas {
    position: relative;
    width: 1200px;
    height: 900px;
  }
  .business-card {
    position: absolute;
    left: 180px;
    top: 210px;
    width: 840px;
    height: 480px;
    border-radius: 4px;
    overflow: hidden;
    box-shadow: 0 18px 40px rgba(0,0,0,0.22), 0 3px 8px rgba(0,0,0,0.15);
  }
  .card-shapes {
    position: absolute;
    inset: 0;
    width: 100%;
    height: 100%;
    display: block;
  }
  .brand-lockup {
    position: absolute;
    left: 60px;
    top: 205px;
    display: flex;
    align-items: center;
    gap: 14px;
  }
  .brand-dot {
    width: 26px;
    height: 26px;
    border-radius: 50%;
    background: var(--brand-blue);
    flex: none;
  }
  .brand-name {
    font-weight: 700;
    font-size: 38px;
    letter-spacing: 0.5px;
    color: var(--brand-green);
    line-height: 1;
    white-space: nowrap;
  }
  .contact-block {
    position: absolute;
    left: 520px;
    top: 150px;
    color: var(--text-light);
  }
  .person-name {
    font-weight: 700;
    font-size: 23px;
    line-height: 1.2;
  }
  .person-title {
    font-weight: 400;
    font-size: 17px;
    color: var(--text-soft);
    margin-top: 3px;
  }
  .contact-list {
    list-style: none;
    margin-top: 34px;
  }
  .contact-item {
    display: flex;
    align-items: center;
    gap: 16px;
    font-size: 18px;
    line-height: 1;
    margin-bottom: 14px;
  }
  .contact-icon {
    width: 15px;
    height: 15px;
    flex: none;
    fill: var(--text-light);
  }
</style>
</head>
<body>
<main class="canvas">
  <article class="business-card" aria-label="Business card for Qorvel Studies">
    <svg class="card-shapes" viewBox="0 0 840 480" aria-hidden="true">
      <defs>
        <linearGradient id="darkPanel" x1="0" y1="0" x2="1" y2="1">
          <stop offset="0" stop-color="#2e2e2e"/>
          <stop offset="1" stop-color="#1e1e1e"/>
        </linearGradient>
        <linearGradient id="silverBand" x1="0" y1="0" x2="0" y2="1">
          <stop offset="0" stop-color="#9a9a9a"/>
          <stop offset="0.35" stop-color="#f4f4f4"/>
          <stop offset="0.6" stop-color="#c4c4c4"/>
          <stop offset="1" stop-color="#7e7e7e"/>
        </linearGradient>
      </defs>
      <rect class="dark-panel" width="840" height="480" fill="url(#darkPanel)"/>
      <path class="silver-band" d="M0 0 H372 Q505 240 362 480 H0 Z" fill="url(#silverBand)"/>
      <path class="white-panel" d="M0 0 H346 Q474 240 334 480 H0 Z" fill="#ffffff"/>
    </svg>

    <div class="brand-lockup">
      <span class="brand-dot"></span>
      <span class="brand-name">Qorvel Studies</span>
    </div>

    <section class="contact-block">
      <h1 class="person-name">Bertrand Okonfu</h1>
      <p class="person-title">VP Research and Senior Analyst</p>
      <ul class="contact-list">
        <li class="contact-item">
          <svg class="contact-icon" viewBox="0 0 16 16" aria-label="Phone"><path d="M1 5c0-2 3-3 7-3s7 1 7 3v1.5h-3.5V5H4.5v1.5H1zM3 8h10l1.5 6h-13z"/></svg>
          <span>555-203-4719</span>
        </li>
        <li class="contact-item">
          <svg class="contact-icon" viewBox="0 0 16 16" aria-label="Email"><path d="M1 3h14v1.2L8 9 1 4.2z M1 5.8 8 10.6l7-4.8V13H1z"/></svg>
          <span>info@qorvelstudies.example</span>
        </li>
      </ul>
    </section>
  </article>
</main>
</body>
</html>
```